Restyle Company web site and logo

we need a wordpress design beacause after few year we need to refresh our company web site(www.velotrastudio.example) & logo. We are a small company called VR Advisory focused on business intellegence, data quality, data integration, etc and based on Legnago (small town near to Verona (italy)).
During the 2014 we add to our skill develop project for MDM and Procurement.
We are Young (avg 30 years old). We want to change our logo and color templete to communicate to all cumstomer professional skill, precision and passion.

--- UPDATE --
The new site can be complitile different from the actual website.
The new Logo is now available.
Updates

Target Market(s)

B2B, mid size market, professional account

Industry/Entity Type

It Company

Font styles to use
Sans Serif

Colors
acd037
3277b5

Requirements
Must have
• Simple and clean/clear image colur. Professional site. it need to rapresent trust site.
• Must be responsive desk/mobile.
Nice to have
• different color area for different kind off business line.
• slider image.
Should not have
• classical image

```html
<!DOCTYPE html>
<html lang="it">
<head>
<meta charset="utf-8">
<title>VR Advisory</title>
<link href="https://fonts.googleapis.com/css2?family=Open+Sans:wght@400;600;700&display=swap" rel="stylesheet">
<style>
:root{
  --green:#acd037;
  --green-dark:#8fb52a;
  --blue:#3277b5;
  --band-blue:#11699a;
  --text:#555;
  --text-soft:#888;
  --footer-bg:#f1f1f1;
  --white:#fff;
}
*{margin:0;padding:0;box-sizing:border-box}
html,body{width:889px;height:1200px;overflow:hidden;background:var(--white)}
body{position:relative;font-family:"Open Sans",Arial,sans-serif;color:var(--text)}
.abs{position:absolute}

/* header */
.site-header{left:0;top:0;width:889px;height:44px;background:var(--white)}
.brand{left:165px;top:9px;display:flex;align-items:center;gap:8px}
.brand-dot{width:24px;height:24px;border-radius:50%;background:var(--green)}
.brand-name{font-size:19px;font-weight:600;color:var(--blue);letter-spacing:.5px}
.main-nav{left:441px;top:21px;display:flex;gap:22px;font-size:6.5px;text-transform:uppercase;color:var(--text-soft)}
.main-nav .active{color:var(--blue);font-weight:600}

/* hero */
.hero{left:0;top:44px;width:889px;height:281px;background:linear-gradient(135deg,#e9ecef 0%,#d7dce0 45%,#f1f2f3 70%,#c9ced3 100%)}
.hero-caption{left:0;top:247px;width:889px;height:78px;background:rgba(255,255,255,.72)}
.hero-title{left:163px;top:264px;font-size:13px;font-weight:700;color:var(--blue)}
.hero-sub{left:163px;top:284px;font-size:10px;color:var(--green-dark);font-family:Arial,sans-serif}
.slider-btn{top:272px;width:20px;height:20px;border-radius:50%}
.slider-btn.prev{left:640px;background:#777}
.slider-btn.next{left:665px;background:var(--green)}
.slider-btn svg{display:block}

/* services */
.service{top:355px;width:130px;text-align:center}
.service-icon{display:block;margin:0 auto 6px}
.service-title{font-size:7.5px;text-transform:uppercase;color:#666;line-height:1.35;margin-bottom:6px}
.service-text{font-size:5.5px;color:var(--text-soft);line-height:1.45}

/* feature band */
.feature{left:0;top:473px;width:889px;height:233px;background:linear-gradient(120deg,#a3c833 0%,#b3d540 50%,#9fc22f 100%)}
.feature-inner{left:0;top:538px;width:889px;text-align:center}
.feature-title{font-size:16px;color:var(--white);font-weight:400}
.feature-link{font-size:5.5px;color:var(--white);font-weight:700;margin-top:4px}
.feature-text{font-size:7.5px;color:#3c4a14;line-height:1.55;margin:10px auto 0;width:380px}
.feature-btn{left:394px;top:624px;width:61px;height:17px;border:1px solid var(--white);color:var(--white);font-size:5.5px;text-align:center;line-height:15px;text-transform:uppercase}

/* references */
.refs-head{left:0;top:740px;width:889px;text-align:center}
.refs-title{font-size:16px;color:#666;font-weight:400}
.refs-sub{font-size:6.5px;color:var(--blue);margin-top:4px}
.ref-card{top:792px;width:123px}
.ref-img{width:123px;height:78px}
.ref-label{font-size:7.5px;color:var(--blue);text-align:center;margin-top:8px;padding-bottom:5px;border-bottom:1px solid var(--blue)}
.carousel-arrow{top:831px;width:18px;height:18px;border-radius:50%;background:#e4e4e4}

/* people band */
.people-band{left:0;top:917px;width:889px;height:68px;background:var(--band-blue);text-align:center;color:var(--white)}
.people-band p{font-size:10.5px;margin-top:20px}
.people-band a{display:inline-block;font-size:7.5px;color:var(--white);text-decoration:underline;margin-top:3px}

/* footer */
.site-footer{left:0;top:985px;width:889px;height:185px;background:var(--footer-bg)}
.footer-brand{left:165px;top:1012px;display:flex;align-items:center;gap:5px}
.footer-brand .brand-dot{width:14px;height:14px}
.footer-brand .brand-name{font-size:9px}
.footer-about{left:165px;top:1054px;width:175px;font-size:5.5px;line-height:1.6;color:#555}
.col-title{font-size:16px;color:var(--blue);font-weight:400}
.news{left:373px;top:1006px;width:125px}
.news-item{border-bottom:1px solid #ccc;padding:8px 0 6px}
.news-item h4{font-size:6px;color:#555;font-weight:700}
.news-item p{font-size:4.8px;color:var(--text-soft);line-height:1.5;margin-top:6px}
.news-all{font-size:4.5px;color:#555;font-weight:700;text-transform:uppercase;margin-top:6px;text-decoration:underline}
.contact{left:556px;top:1006px;width:120px}
.contact h5{font-size:6px;color:#555;font-weight:700;text-transform:uppercase;margin-top:12px}
.contact p{font-size:5.5px;color:#555;line-height:1.75;margin-top:16px}
.live-chat{left:686px;top:1040px;width:24px;height:85px;background:#5b5b5b;border:1px solid #999;border-radius:2px}
.live-chat span{position:absolute;left:5px;top:78px;transform:rotate(-90deg);transform-origin:0 0;font-size:8px;color:var(--white);white-space:nowrap;width:70px;text-align:center}

/* bottom bar */
.bottom-bar{left:0;top:1170px;width:889px;height:30px;background:var(--white)}
.copyright{left:165px;top:1181px;font-size:5px;color:var(--text-soft)}
.social{left:633px;top:1178px;display:flex;gap:4px}
.social span{width:10px;height:10px;border-radius:2px}
</style>
</head>
<body>

<header class="site-header abs">
  <div class="brand abs" style="left:165px;top:9px;position:absolute">
    <span class="brand-dot"></span><span class="brand-name">VR ADVISORY</span>
  </div>
  <nav class="main-nav abs">
    <span class="active">Home</span><span>Business Partner</span><span>Reference</span><span>Collaboration</span><span>Contact us</span>
  </nav>
</header>

<section class="hero abs" role="img" aria-label="Photo of a pen resting on printed financial reports and a pie chart"></section>
<div class="hero-caption abs"></div>
<h1 class="hero-title abs">Corporate Performance Management</h1>
<p class="hero-sub abs">E' un insieme di processi che aiutano le organizzazioni ad ottimizzare le prestazioni del business...</p>
<span class="slider-btn prev abs"><svg width="20" height="20" viewBox="0 0 20 20"><path d="M11.5 6 L7.5 10 L11.5 14" stroke="#fff" stroke-width="1.6" fill="none"/></svg></span>
<span class="slider-btn next abs"><svg width="20" height="20" viewBox="0 0 20 20"><path d="M8.5 6 L12.5 10 L8.5 14" stroke="#fff" stroke-width="1.6" fill="none"/></svg></span>

<div class="service abs" style="left:195px">
  <svg class="service-icon" width="24" height="24" viewBox="0 0 24 24"><circle cx="12" cy="12" r="11" fill="none" stroke="#666" stroke-width="1"/><rect x="7" y="7" width="10" height="10" fill="none" stroke="#666" stroke-width="1"/><path d="M9 12.5 L11 14.5 L15 9.5" fill="none" stroke="#666" stroke-width="1"/></svg>
  <h3 class="service-title">Business Intelligence</h3>
  <p class="service-text">Non lasciare che i problemi frenino il tuo business. Evolution support nasce con lo scopo di aiutare i nostri clienti in tutti i momenti</p>
</div>
<div class="service abs" style="left:359px">
  <svg class="service-icon" width="24" height="24" viewBox="0 0 24 24"><path d="M12 1.5 L14.6 4 L18 3.6 L18.8 7 L21.8 8.8 L20.6 12 L21.8 15.2 L18.8 17 L18 20.4 L14.6 20 L12 22.5 L9.4 20 L6 20.4 L5.2 17 L2.2 15.2 L3.4 12 L2.2 8.8 L5.2 7 L6 3.6 L9.4 4 Z" fill="none" stroke="#666" stroke-width="1"/><path d="M8 12 L11 15 L16 9" fill="none" stroke="#666" stroke-width="1.2"/></svg>
  <h3 class="service-title">Corporate Performance<br>Management ( CPM )</h3>
  <p class="service-text">E' un insieme di processi che aiutano le organizzazioni ad ottimizzare le prestazioni del business (viene visto come una Business Intelligence</p>
</div>
<div class="service abs" style="left:524px">
  <svg class="service-icon" width="24" height="24" viewBox="0 0 24 24"><circle cx="12" cy="12" r="11" fill="none" stroke="#666" stroke-width="1"/><rect x="8" y="11" width="8" height="7" fill="none" stroke="#666" stroke-width="1"/><path d="M9.5 11 V8.5 a2.5 2.5 0 0 1 5 0 V11" fill="none" stroke="#666" stroke-width="1"/></svg>
  <h3 class="service-title">Evolution Support</h3>
  <p class="service-text">L'informazione che guida il tuo business. Quante persone all'interno della vostra azienda hanno l'informazione giusta, al momento giusto</p>
</div>

<section class="feature abs" role="img" aria-label="Green tinted photo of a laptop keyboard, coffee cup and notes on a desk"></section>
<div class="feature-inner abs">
  <h2 class="feature-title">Quadra MIT</h2>
  <p class="feature-link">Sito ufficiale Quadra MIT: www.quadrasoft.example</p>
  <p class="feature-text">QUADRA è il software che unifica Business Intelligence e Performance Management in un unico ambiente integrato che permette il controllo e la gestione dei processi</p>
</div>
<a class="feature-btn abs">Read more</a>

<div class="refs-head abs">
  <h2 class="refs-title">Our Referenze</h2>
  <p class="refs-sub">I settori principali nei quali abbiamo operato sono</p>
</div>
<span class="carousel-arrow abs" style="left:150px"></span>
<span class="carousel-arrow abs" style="left:682px"><svg width="18" height="18" viewBox="0 0 18 18"><path d="M7.5 5 L11 9 L7.5 13" stroke="#fff" stroke-width="1.5" fill="none"/></svg></span>
<div class="ref-card abs" style="left:163px">
  <div class="ref-img" role="img" aria-label="Photo of a smartphone showing a colourful app" style="background:linear-gradient(135deg,#f3f3f3,#9fb3c4 60%,#e07a3a)"></div>
  <p class="ref-label">mobile e arredamento</p>
</div>
<div class="ref-card abs" style="left:296px">
  <div class="ref-img" role="img" aria-label="Photo of a chef plating a dish" style="background:linear-gradient(135deg,#f2ede4,#d6a56a 55%,#8e5a2e)"></div>
  <p class="ref-label">food &amp; beverage</p>
</div>
<div class="ref-card abs" style="left:430px">
  <div class="ref-img" role="img" aria-label="Photo of engineers in a factory setting" style="background:linear-gradient(135deg,#e4e7ea,#9aa3ab 55%,#6b747c)"></div>
  <p class="ref-label">manufacturing</p>
</div>
<div class="ref-card abs" style="left:563px">
  <div class="ref-img" role="img" aria-label="Photo of a telecom tower against a blue sky" style="background:linear-gradient(135deg,#3f82c8,#8fbde6 55%,#e9f1f8)"></div>
  <p class="ref-label">telecomunicazioni</p>
</div>

<section class="people-band abs">
  <p>We Just Want to have &nbsp;GREAT PEOPLE working for us</p>
  <a>Click for more detail</a>
</section>

<footer class="site-footer abs"></footer>
<div class="footer-brand abs"><span class="brand-dot"></span><span class="brand-name">VR ADVISORY</span></div>
<p class="footer-about abs">Quante persone all'interno della vostra azienda hanno l'informazione desiderata, nel momento giusto e nella forma corretta?<br>Per un'azienda è fondamentale sfruttare le informazioni di cui dispone rendendole consultabili ai propri manager al fine di aiutarli nelle scelte strategiche aziendali, capire l'andamento delle performance dell'azienda, generare stime previsionali, ipotizzare scenari futuri e strategie di risposta.</p>

<div class="news abs">
  <h2 class="col-title">In the News</h2>
  <div class="news-item"><h4>Lumen Report 2011</h4><p>Come puoi consentire alle persone di prendere decisioni migliori e più rapide aumentando la loro produttività?</p></div>
  <div class="news-item"><h4>Lumen Report 2011</h4><p>Come puoi consentire alle persone di prendere decisioni migliori e più rapide aumentando la loro produttività?</p></div>
  <p class="news-all">View all news</p>
</div>

<div class="contact abs">
  <h2 class="col-title">Contact Info</h2>
  <h5>Sede legale</h5>
  <p>Via delle Rogge, 14/B<br>37099 Borgoleo (VR)<br>Italy</p>
  <h5>Sede operativa di Borgoleo</h5>
  <p>Via delle Rogge, 102<br>37099 Borgoleo (VR)<br>Tel 0442 - 5550198<br>Fax 0442 - 5550195</p>
</div>

<div class="live-chat abs"><span>Live Chat Now!</span></div>

<div class="bottom-bar abs"></div>
<p class="copyright abs">© Copyright VR Advisory S.r.l. 2014. All Rights Reserved</p>
<div class="social abs">
  <span style="background:#3b5a9a"></span><span style="background:#2ea7e0"></span><span style="background:#444"></span><span style="background:#f08a24"></span>
</div>

</body>
</html>
```